Brand new letterhead, business card, email signature etc.

We are a financial company in London, UK. Our website is www.marlowvane.com. We're wanting a complete remodel of the company colours, letter head, business cards, email signatures, etc. Looking to keep the same font for the company name. I have upload a colour palette that we want to work with. We're looking for company letterhead for outgoing letters/ correspondence, letterhead for internal documentation, email signatures, e-letters. etc. Ultimately we will redesign the entire website also. It is important that our clients get a strong, secure, warm, trustworthy, solid feeling and first impression.
Updates

Designs look the same

Target Market(s)

Institutional investors, (ultra) high net worth individuals

Industry/Entity Type

Finance, Invesments banking.

Font styles to use
Other font styles liked:
• Current font is "Champagne & Limousines"

Requirements
Must have
• Must use the colours provided on the PDF uploaded to the portal. The purple = main colour. The red = accent colour.
Nice to have
• Nice to use same font as now for the company name "Corvane". Font is "Champagne & Limousines". Nice to have some reference to the old logo flower, but only subtle.
Should not have
• Do not use the colour red from our website. Use the colours provided on the colour palette PDF that I uploaded in the portal.

```html
<!DOCTYPE html>
<html lang="en">
<head>
<meta charset="utf-8">
<title>Corvane Letterhead</title>
<link href="https://fonts.googleapis.com/css2?family=Jost:wght@300;400;500&display=swap" rel="stylesheet">
<style>
  :root {
    --page: #ffffff;
    --header-tint: #faf8f7;
    --frame: #8f8a8b;
    --rule-grey: #cfc8c9;
    --side-band: #d9cfd1;
    --plum: #4e3b40;
    --ink: #3a2f33;
    --accent: #ea8872;
    --accent-soft: #f3c3b4;
    --petal-lilac: #efe7ea;
    --petal-peach: #fbe6de;
  }
  html, body {
    margin: 0;
    width: 1000px;
    height: 1200px;
    overflow: hidden;
    background: var(--page);
  }
  .canvas {
    position: relative;
    width: 1000px;
    height: 1200px;
  }
  .letterhead {
    position: absolute;
    left: 205px;
    top: 183px;
    width: 590px;
    height: 834px;
    border: 1px solid var(--frame);
    background: var(--page);
    overflow: hidden;
  }
  .header-band {
    position: absolute;
    left: 0; top: 0;
    width: 590px;
    height: 130px;
    background: var(--header-tint);
  }
  .brand {
    position: absolute;
    left: 42px;
    top: 59px;
    display: flex;
    align-items: center;
    gap: 9px;
  }
  .brand-square {
    width: 30px;
    height: 30px;
    border: 1px solid var(--plum);
    box-sizing: border-box;
  }
  .brand-name {
    font-family: "Jost", sans-serif;
    font-weight: 300;
    font-size: 19px;
    letter-spacing: 3.4px;
    color: var(--plum);
    text-transform: uppercase;
  }
  .contact-box {
    position: absolute;
    left: 295px;
    top: 82px;
    width: 203px;
    height: 48px;
    border: 1px solid var(--rule-grey);
    border-bottom: none;
    box-sizing: border-box;
    padding: 5px 0 0 5px;
  }
  .contact-line {
    display: flex;
    align-items: center;
    gap: 5px;
    height: 12px;
    font-family: "Jost", sans-serif;
    font-weight: 500;
    font-size: 5.2px;
    color: var(--ink);
    white-space: nowrap;
  }
  .contact-line svg { width: 10px; height: 10px; flex: none; }
  .contact-line .spacer { width: 10px; flex: none; }
  .floral-panel {
    position: absolute;
    left: 498px;
    top: 0;
    width: 92px;
    height: 82px;
    border-left: 1px solid var(--rule-grey);
    background: radial-gradient(circle at 70% 45%, #e4d9dd 0%, var(--petal-lilac) 45%, var(--header-tint) 100%);
  }
  .floral-strips {
    position: absolute;
    left: 498px;
    top: 82px;
    width: 92px;
    height: 48px;
    border-left: 1px solid var(--rule-grey);
    border-top: 1px solid var(--accent-soft);
    box-sizing: border-box;
    background: linear-gradient(180deg, var(--petal-peach) 0%, #fdf2ee 50%, var(--petal-lilac) 100%);
  }
  .side-band {
    position: absolute;
    left: 0;
    top: 130px;
    width: 16px;
    height: 704px;
    background: var(--side-band);
  }
  .footer-rule {
    position: absolute;
    left: 295px;
    top: 810px;
    width: 295px;
    height: 1px;
    background: var(--accent-soft);
  }
  .footer-web {
    position: absolute;
    left: 296px;
    top: 812px;
    font-family: "Jost", sans-serif;
    font-weight: 500;
    font-size: 7.5px;
    color: var(--ink);
  }
</style>
</head>
<body>
<div class="canvas">
  <div class="letterhead">
    <div class="header-band"></div>

    <div class="brand">
      <div class="brand-square"></div>
      <div class="brand-name">Corvane</div>
    </div>

    <div class="contact-box">
      <div class="contact-line">
        <svg viewBox="0 0 10 10" aria-hidden="true">
          <circle cx="5" cy="5" r="4.5" fill="none" stroke="var(--accent)" stroke-width="0.6"/>
          <path d="M5 2.2a1.8 1.8 0 0 1 1.8 1.8c0 1.3-1.8 3.4-1.8 3.4S3.2 5.3 3.2 4A1.8 1.8 0 0 1 5 2.2z" fill="none" stroke="var(--accent)" stroke-width="0.6"/>
          <circle cx="5" cy="4" r="0.6" fill="var(--accent)"/>
        </svg>
        Corvane (IOM) Limited, Tarrow House, Ramsey, Isle of Man, IM8 4QT
      </div>
      <div class="contact-line">
        <span class="spacer"></span>
        Corvane Group Limited, 9th Floor, 14 Ludgate Row, London, EC4M 7PN
      </div>
      <div class="contact-line">
        <svg viewBox="0 0 10 10" aria-hidden="true">
          <rect x="1" y="2.5" width="8" height="5.5" fill="none" stroke="var(--accent)" stroke-width="0.7"/>
          <path d="M1 2.5l4 3 4-3" fill="none" stroke="var(--accent)" stroke-width="0.7"/>
        </svg>
        info@marlowvane.com
      </div>
    </div>

    <div class="floral-panel" role="img" aria-label="Fine line drawing of an open flower with long stamens in soft lilac"></div>
    <div class="floral-strips" role="img" aria-label="Banded strip of line-drawn petals and stamens in peach and lilac"></div>

    <div class="side-band"></div>

    <div class="footer-rule"></div>
    <div class="footer-web">www.marlowvane.com</div>
  </div>
</div>
</body>
</html>
```